Brightmill Data Works

Our company is about IT hardwares and IT solutions. IT hardware such as PC, RAMS, storage and servers. IT solutions such as project management, BA. We are also selling new technology too.

Target Market(s)

Consumer, Small to Medium Business, Corporate

Requirements
Must have
• The business card must have the following:
• Name:
• Title:
• Contact Number:
• Email address:
• Website:
• Color: Must match the logo color upgrade

```html
<!DOCTYPE html>
<html lang="en">
<head>
<meta charset="utf-8">
<title>Brightmill Data Works – Business Card</title>
<link href="https://fonts.googleapis.com/css2?family=Lato:wght@400;700;900&display=swap" rel="stylesheet">
<style>
  :root {
    --stage: #2b2b2b;
    --card-dark: #1c1c1c;
    --card-light: #ffffff;
    --amber: #e0963a;
    --ink: #3a3a3a;
    --ink-soft: #2a2a2a;
    --paper-text: #f2f2f2;
  }
  * { margin: 0; padding: 0; box-sizing: border-box; }
  html, body { width: 1200px; height: 900px; overflow: hidden; }
  body {
    background: var(--stage);
    font-family: "Lato", sans-serif;
    position: relative;
  }
  .card {
    position: absolute;
    left: 250px;
    width: 700px;
    height: 400px;
    overflow: hidden;
  }
  .card--front { top: 35px; background: var(--card-dark); }
  .card--back { top: 465px; background: var(--card-light); }

  /* Front */
  .front-brand {
    position: absolute; top: 130px; left: 0; width: 100%;
    display: flex; flex-direction: column; align-items: center; gap: 18px;
  }
  .brand-mark {
    width: 34px; height: 34px; border-radius: 50%; background: var(--amber);
  }
  .front-brand .brand-name {
    font-weight: 900; font-size: 44px; letter-spacing: 1px;
    color: var(--paper-text); text-transform: uppercase;
  }
  .front-web {
    position: absolute; bottom: 70px; width: 100%; text-align: center;
    color: var(--paper-text); font-size: 17px; letter-spacing: 0.5px;
  }

  /* Back */
  .swoosh { position: absolute; top: 0; left: 0; }
  .back-brand {
    position: absolute; left: 60px; top: 120px;
    display: flex; align-items: center; gap: 14px;
  }
  .back-brand .brand-name {
    font-weight: 900; font-size: 34px; color: var(--ink); text-transform: uppercase;
    letter-spacing: 0.5px;
  }
  .person { position: absolute; left: 60px; top: 210px; }
  .person-name { color: var(--amber); font-size: 28px; font-weight: 400; }
  .person-title { color: var(--ink-soft); font-size: 18px; margin-top: 2px; }
  .address {
    position: absolute; left: 60px; bottom: 40px;
    color: var(--ink-soft); font-size: 18px; line-height: 1.3;
  }
  .contacts {
    position: absolute; right: 50px; top: 200px;
    list-style: none; color: var(--ink-soft); font-size: 17px;
  }
  .contacts li { display: flex; align-items: center; gap: 12px; line-height: 1.45; }
  .contacts svg { width: 16px; height: 16px; fill: var(--amber); flex: none; }
</style>
</head>
<body>

<section class="card card--front">
  <div class="front-brand">
    <span class="brand-mark"></span>
    <span class="brand-name">Brightmill Data Works</span>
  </div>
  <p class="front-web">www.brightmilldata.com</p>
</section>

<section class="card card--back">
  <svg class="swoosh" width="700" height="400" viewBox="0 0 700 400" aria-hidden="true">
    <path d="M240 0 H700 V130 Q560 40 240 0 Z" fill="var(--card-dark)"/>
    <path d="M240 0 Q560 40 700 130 V150 Q600 70 420 50 Q320 30 240 0 Z" fill="var(--amber)"/>
  </svg>

  <div class="back-brand">
    <span class="brand-mark"></span>
    <span class="brand-name">Brightmill Data Works</span>
  </div>

  <div class="person">
    <p class="person-name">Daniel Ashcombe</p>
    <p class="person-title">Manager</p>
  </div>

  <p class="address">418 Larkfield Road<br>Houston, TX 77041</p>

  <ul class="contacts">
    <li>
      <svg viewBox="0 0 16 16"><path d="M3 1h3l1.5 4-2 1.3a9 9 0 0 0 4.2 4.2L11 8.5l4 1.5v3c0 1-1 2-2 2A12 12 0 0 1 1 3c0-1 1-2 2-2z"/></svg>
      512 555 0148
    </li>
    <li>
      <svg viewBox="0 0 16 16"><path d="M4 1h8v4H4zM1 6h14v6h-3v3H4v-3H1zM5 10v3h6v-3z"/></svg>
      512 555 0149
    </li>
    <li>
      <svg viewBox="0 0 16 16"><path d="M1 3h14v10H1zM2 4l6 5 6-5v-.2H2z" fill-rule="evenodd"/></svg>
      info@brightmilldata.com
    </li>
    <li>
      <svg viewBox="0 0 16 16"><path d="M8 1a7 7 0 1 0 0 14A7 7 0 0 0 8 1zm0 1.5c1 1 1.6 2.5 1.8 4.5H6.2C6.4 5 7 3.5 8 2.5zM2.6 7h2.1c.1-1.6.5-3 1.1-4A5.5 5.5 0 0 0 2.6 7zm8.7 0h2.1a5.5 5.5 0 0 0-3.2-4c.6 1 1 2.4 1.1 4zM2.6 9a5.5 5.5 0 0 0 3.2 4c-.6-1-1-2.4-1.1-4zm3.6 0c.2 2 .8 3.5 1.8 4.5 1-1 1.6-2.5 1.8-4.5zm5.1 0c-.1 1.6-.5 3-1.1 4a5.5 5.5 0 0 0 3.2-4z"/></svg>
      www.brightmilldata.com
    </li>
  </ul>
</section>

</body>
</html>
```